School Hallway Magnetic Display Design for school values

I am looking for a someone to help me design a magnetic hallway display that will hang in the hallway of our small school. There are several elements, including 1. 6ft by 4ft designed magnetic bulletin board, 2. Magnets that will stick to the board. See attachment for which elements belong where. The display will be for our MOBLAT program, which rewards students for demonstrating our school values. We want the display to be beautiful and interactive. We are also rebranding, so we want the design to align with our new fonts and colors. In the attached PDF is an outline of our new brand guidelines. Unfortunately, we don't have the color codes, but I'm hoping that you can match the colors listed. Attached are elements to be used on the board, but please use your creativity to make it more dynamic and visually appealing. For example, the star magnets could be another shape. The MOBLAT magnets must remain the same. I've included two photos of boards at other schools that inspired this project.

Target Market(s)

School Community

Industry/Entity Type

Education

Requirements
Should not have
• School Logo

```html
<!DOCTYPE html>
<html lang="en">
<head>
<meta charset="utf-8">
<title>MOBLAT of the Month – Hallway Display</title>
<link href="https://fonts.googleapis.com/css2?family=DM+Serif+Display&family=Montserrat:wght@600;800&display=swap" rel="stylesheet">
<style>
  :root {
    --canvas: #ffffff;
    --cream: #f8f6e6;
    --deep-green: #1f5c3a;
    --forest: #2f7d45;
    --leaf: #4f9a3a;
    --teal: #5fae92;
    --mint: #8fd48a;
    --line-green: #3d9a4e;
    --gold: #c9a93a;
    --olive: #8a9a2c;
    --ink: #1b1b1b;
  }
  html, body {
    margin: 0;
    width: 1200px;
    height: 1200px;
    overflow: hidden;
    background: var(--canvas);
  }
  .display {
    position: absolute;
    left: 60px;
    top: 270px;
    width: 1080px;
    height: 660px;
  }
  .title-text { font-family: "DM Serif Display", Georgia, serif; font-size: 60px; fill: var(--ink); }
  .whiteboard-label { font-family: "DM Serif Display", Georgia, serif; font-size: 50px; fill: var(--mint); letter-spacing: 1px; }
  .dimension-label { font-family: "Montserrat", Arial, sans-serif; font-weight: 800; font-size: 22px; fill: var(--line-green); }
  .value-text { font-family: "Montserrat", Arial, sans-serif; font-weight: 800; font-size: 19px; fill: var(--ink); letter-spacing: 0.5px; }
</style>
</head>
<body>
<svg class="display" viewBox="375 133 1200 733" xmlns="http://www.w3.org/2000/svg">
  <defs>
    <linearGradient id="border-tones" x1="0" y1="0" x2="1" y2="1">
      <stop offset="0" stop-color="#6f8f3a"/>
      <stop offset="0.35" stop-color="#2f6b3c"/>
      <stop offset="0.7" stop-color="#a7a23a"/>
      <stop offset="1" stop-color="#3b6e46"/>
    </linearGradient>
    <linearGradient id="progress-tones" x1="0" y1="0" x2="0" y2="1">
      <stop offset="0" stop-color="#dfe6d2"/>
      <stop offset="1" stop-color="#9fbfa6"/>
    </linearGradient>
    <marker id="arrow-head" viewBox="0 0 10 10" refX="8" refY="5" markerWidth="7" markerHeight="7" orient="auto-start-reverse">
      <path d="M0 0 L10 5 L0 10 Z" fill="var(--line-green)"/>
    </marker>
    <polygon id="star" points="0,-24 7,-7.5 25,-7.5 10.5,3.5 15.5,21 0,11 -15.5,21 -10.5,3.5 -25,-7.5 -7,-7.5"/>
  </defs>

  <!-- patterned border -->
  <rect class="board-border" x="375" y="133" width="1200" height="733" fill="url(#border-tones)" role="img" aria-label="Green and gold geometric pattern border"/>

  <!-- cream board surface -->
  <polygon class="board-surface" points="397,152 1555,152 1555,834 397,836" fill="var(--cream)"/>

  <!-- title ribbon -->
  <g class="title-ribbon">
    <polygon points="452,292 530,210 1250,198 1248,212 1310,230 1240,300 760,292" fill="var(--forest)"/>
    <polygon points="520,232 1280,212 1300,238 1252,290 530,296" fill="var(--gold)" opacity="0.85"/>
    <polygon points="475,264 540,218 1270,220 1250,288 540,284" fill="var(--teal)"/>
    <text class="title-text" x="882" y="270" text-anchor="middle">MOBLAT of the Month</text>
  </g>

  <!-- whiteboard area -->
  <g class="whiteboard">
    <rect x="493" y="328" width="801" height="374" fill="#fbfcf6" stroke="#b7dcc0" stroke-width="1.5" role="img" aria-label="Faint green line pattern on whiteboard surface"/>
    <text class="whiteboard-label" x="910" y="518" text-anchor="middle">White Board</text>
  </g>

  <!-- dimensions -->
  <g class="dimensions">
    <line x1="460" y1="470" x2="460" y2="330" stroke="var(--line-green)" stroke-width="2" marker-end="url(#arrow-head)"/>
    <line x1="460" y1="560" x2="460" y2="700" stroke="var(--line-green)" stroke-width="2" marker-end="url(#arrow-head)"/>
    <text class="dimension-label" transform="translate(468 505) rotate(-90)" text-anchor="middle">48 in</text>
    <line x1="830" y1="729" x2="495" y2="729" stroke="var(--line-green)" stroke-width="2" marker-end="url(#arrow-head)"/>
    <line x1="955" y1="729" x2="1292" y2="729" stroke="var(--line-green)" stroke-width="2" marker-end="url(#arrow-head)"/>
    <text class="dimension-label" x="893" y="737" text-anchor="middle">72 in</text>
  </g>

  <!-- progress tracker artwork area -->
  <rect class="progress-artwork" x="1352" y="197" width="134" height="228" rx="10" fill="url(#progress-tones)" role="img" aria-label="Green thermometer illustration tracking progress"/>

  <!-- value magnets -->
  <g class="value-magnets">
    <rect x="1316" y="438" width="207" height="32" rx="3" fill="#e9f3e8" stroke="var(--teal)" stroke-width="4"/>
    <text class="value-text" x="1419" y="461" text-anchor="middle">Simplicity</text>
    <rect x="1316" y="476" width="207" height="32" rx="3" fill="#eef6ec" stroke="#7cc6a4" stroke-width="4"/>
    <text class="value-text" x="1419" y="499" text-anchor="middle">Peace</text>
    <rect x="1316" y="512" width="207" height="32" rx="3" fill="#eef6ec" stroke="var(--forest)" stroke-width="4"/>
    <text class="value-text" x="1419" y="535" text-anchor="middle">Integrity</text>
    <rect x="1316" y="549" width="207" height="32" rx="3" fill="#f3f6ee" stroke="var(--deep-green)" stroke-width="4"/>
    <text class="value-text" x="1419" y="572" text-anchor="middle">Community</text>
    <rect x="1316" y="589" width="207" height="32" rx="3" fill="#eef3dc" stroke="var(--olive)" stroke-width="4"/>
    <text class="value-text" x="1419" y="612" text-anchor="middle">Equality</text>
    <rect x="1316" y="629" width="207" height="32" rx="3" fill="#e9f3ee" stroke="#4b9a86" stroke-width="4"/>
    <text class="value-text" x="1419" y="652" text-anchor="middle">Stewardship</text>
  </g>

  <!-- star magnets -->
  <g class="star-magnets" fill="var(--gold)" stroke="#a8872a" stroke-width="1.5">
    <use href="#star" x="1345" y="696"/>
    <use href="#star" x="1419" y="696"/>
    <use href="#star" x="1494" y="696"/>
    <use href="#star" x="1345" y="741"/>
    <use href="#star" x="1419" y="741"/>
    <use href="#star" x="1494" y="741"/>
    <use href="#star" x="1345" y="786"/>
    <use href="#star" x="1435" y="786"/>
  </g>
</svg>
</body>
</html>
```